Logistics Website Design

See website https://tqfreightglobal.com for theme and color details. Need the site to be re-done and reflect some of the designs shown in this list here: https://pixelvane.com/tags/logistics-company-website

Target Market(s)

Logistics & Transportation

Industry/Entity Type

Logistics and Supply Chain

Coding

Number of Pages Required

5+ page

Requirements
Must have
• Colors must match theme of logo. Looking for a sleek, interactive design.

```html
<!DOCTYPE html>
<html lang="en">
<head>
<meta charset="utf-8">
<title>TQ Freight Global — Logistics</title>
<link href="https://fonts.googleapis.com/css2?family=Inter:wght@400;500;600;700;800;900&display=swap" rel="stylesheet">
<style>
:root{
  --orange:#f94d12;
  --brown:#6a1d0a;
  --dark:#111;
  --ink:#1b1b1b;
  --pink:#f9d7cb;
  --salmon:#f0a78c;
  --footer:#2b2624;
  --white:#fff;
  --muted:#444;
}
*{box-sizing:border-box;margin:0;padding:0}
html,body{width:1200px;height:3643px;overflow:hidden}
body{position:relative;font-family:"Inter",Arial,sans-serif;color:var(--ink);background:var(--white)}
.abs{position:absolute}
.photo{position:absolute}
.hl{font-weight:900;text-transform:uppercase;letter-spacing:-.5px;line-height:1.12}
.hl em{font-style:normal;color:var(--brown)}
.btn{display:inline-block;background:var(--orange);color:#fff;font-weight:700;border-radius:8px;outline:2px solid var(--orange);outline-offset:3px}

/* nav */
.nav{left:0;top:0;width:1200px;height:88px;background:var(--dark)}
.brand{left:34px;top:26px;display:flex;align-items:center;gap:8px;color:var(--orange);font-weight:800;font-size:15px}
.brand i{width:22px;height:22px;border-radius:50%;background:var(--orange)}
.menu{left:173px;top:36px;display:flex;gap:44px;color:#fff;font-size:15px}
.menu span small{font-size:10px;margin-left:8px}
.call{left:807px;top:0;width:232px;height:88px;background:#fff;display:flex;align-items:center;gap:12px;padding-left:26px}
.call .lbl{color:var(--orange);font-size:15px;line-height:1.2}
.call .lbl b{display:block;font-size:21px;font-weight:700}
.contact-top{left:1039px;top:0;width:161px;height:88px;background:var(--orange);color:#fff;font-weight:700;font-size:17px;text-align:center;padding-top:26px}

/* hero */
.hero-title{left:88px;top:234px;font-size:45px;color:var(--ink)}
.hero-sub{left:88px;top:398px;width:330px;font-size:16px}
.hero-btn{left:92px;top:452px;padding:12px 20px;font-size:17px}

/* about */
.about-title{left:600px;top:718px;font-size:40px}
.about-text{left:600px;top:880px;width:435px;font-size:16.5px;line-height:1.2}
.about-btn{left:604px;top:1057px;padding:12px 23px;font-size:16px}

/* services */
.svc-bg{left:511px;top:1232px;width:689px;height:668px;background:var(--pink)}
.svc-title{left:567px;top:1288px;font-size:42px}
.svc-text{left:567px;top:1346px;width:545px;font-size:16.5px;line-height:1.2;color:var(--muted)}
.svc-text p+p{margin-top:10px}
.svc-cards{left:263px;top:1565px;width:887px;height:266px;background:#fff;border-radius:12px;display:flex;padding:28px 0 0 22px}
.svc-card{width:220px;padding:0 20px;border-left:1px solid #ddd}
.svc-card:first-child{border-left:0;padding-left:0}
.svc-ico{width:58px;height:58px;border-radius:12px;background:var(--brown);margin-bottom:20px;display:flex;align-items:center;justify-content:center}
.svc-card h3{font-size:17px;font-weight:800;color:var(--brown);line-height:1.15;margin-bottom:10px}
.svc-card p{font-size:11.5px;line-height:1.25;color:var(--muted)}

/* industries */
.ind-title{left:0;width:1200px;top:1996px;text-align:center;font-size:42px}
.ind-text{left:120px;width:960px;top:2050px;text-align:center;font-size:16.5px;line-height:1.2;color:var(--muted)}
.ind-card{top:2146px;width:187px;height:360px;border-radius:12px;overflow:hidden}
.ind-card .ph{height:295px}
.ind-card .lab{height:65px;display:flex;align-items:center;padding:0 16px;color:#fff;font-weight:800;font-size:16px;line-height:1.2}
.lab.o{background:var(--orange)} .lab.b{background:#2b1208}

/* cta */
.cta-bg{left:0;top:2610px;width:1200px;height:684px;background:var(--pink)}
.cta-title{left:0;width:1200px;top:2655px;text-align:center;font-size:43px}
.cta-sub{left:0;width:1200px;top:2717px;text-align:center;font-size:17px}
.form-card{left:125px;top:2780px;width:950px;height:429px;background:#fff;border-radius:10px;overflow:hidden}
.form-title{left:622px;top:2812px;font-size:43px;color:var(--brown)}
.field{position:absolute;border:2px solid var(--brown);border-radius:8px;font-size:11px;color:var(--orange);padding:16px 12px}
.submit{left:764px;top:3132px;width:143px;height:44px;border-radius:10px;background:var(--orange);color:#fff;font-weight:700;font-size:17px;text-align:center;line-height:44px}

/* footer */
.foot{left:0;top:3294px;width:1200px;height:303px;background:var(--footer)}
.foot-brand{left:76px;top:3378px;display:flex;align-items:center;gap:10px;color:var(--orange);font-weight:800;font-size:20px}
.foot-brand i{width:26px;height:26px;border-radius:50%;background:var(--orange)}
.foot-about{left:75px;top:3476px;width:310px;font-size:11.5px;line-height:1.2;color:#eee}
.col{top:3364px;color:#fff;font-size:15px}
.col h4{color:var(--orange);font-size:17px;font-weight:700;margin-bottom:10px}
.col li{list-style:none;margin-bottom:13px}
.enq li{display:flex;align-items:center;gap:10px;font-weight:700}
.socials{display:flex;gap:24px;margin-top:4px}
.socials span{width:16px;height:16px;background:#fff;border-radius:3px}
.bar{left:0;top:3597px;width:1200px;height:46px;background:var(--orange);color:#fff;font-size:11px}
.bar .l{position:absolute;left:72px;top:17px}
.bar .r{position:absolute;left:880px;top:17px;word-spacing:2px}
</style>
</head>
<body>

<header class="abs nav">
  <div class="abs brand"><i></i>TQ Freight Global</div>
  <nav class="abs menu"><span>Home</span><span>Services<small>⌄</small></span><span>Industries<small>⌄</small></span><span>Request a Quote<small>⌄</small></span><span>About Us</span></nav>
</header>
<div class="abs call">
  <svg width="26" height="38" viewBox="0 0 26 38"><rect x="2" y="2" width="22" height="34" rx="4" fill="none" stroke="#333" stroke-width="2.5"/><line x1="10" y1="31" x2="16" y2="31" stroke="#333" stroke-width="2"/></svg>
  <div class="lbl">Call Us At<b>(415)-555-0142</b></div>
</div>
<div class="abs contact-top">Contact Us
  <svg width="60" height="10" style="display:block;margin:10px auto 0"><line x1="0" y1="5" x2="56" y2="5" stroke="#fff" stroke-width="1.5"/><path d="M52 1 L58 5 L52 9" fill="none" stroke="#fff" stroke-width="1.5"/></svg>
</div>

<!-- hero -->
<svg class="abs" style="left:420px;top:88px" width="780" height="520" viewBox="0 0 780 520">
  <defs><linearGradient id="heroG" x1="0" y1="0" x2="0" y2="1"><stop offset="0" stop-color="#cfd9e2"/><stop offset=".45" stop-color="#4f6f4a"/><stop offset=".7" stop-color="#8a8a86"/><stop offset="1" stop-color="#b48a3e"/></linearGradient></defs>
  <polygon points="270,0 780,0 780,514 300,514 190,360 260,250" fill="url(#heroG)" role="img" aria-label="Photo of a white semi truck on a highway beside a lake and forested hills"/>
  <polygon points="130,0 270,0 195,195 60,160" fill="var(--orange)"/>
  <polygon points="270,0 305,0 195,195 180,185" fill="#7a2a10"/>
  <polygon points="40,160 110,180 60,300 150,470 110,520 10,320" fill="var(--salmon)"/>
  <polygon points="150,360 190,360 290,520 200,520 135,430" fill="var(--orange)"/>
</svg>
<h1 class="abs hl hero-title">Delivering<br><em>Strength</em><br>in Every Mile</h1>
<p class="abs hero-sub">Secure and reliable transportation for all your cargo needs.</p>
<span class="abs btn hero-btn">Request a Quote</span>

<!-- about -->
<div class="photo" style="left:125px;top:699px;width:396px;height:429px;border-radius:8px;background:linear-gradient(180deg,#4a5870 0%,#e28a4c 35%,#8a6a55 60%,#5d5d62 100%)" role="img" aria-label="Photo of a white truck on a highway at sunset"></div>
<div class="photo" style="left:334px;top:936px;width:214px;height:214px;background:#fff"></div>
<div class="photo" style="left:346px;top:945px;width:196px;height:200px;background:linear-gradient(160deg,#c9d3de 0%,#a54a3a 45%,#3d5a7a 75%,#6a6a70 100%)" role="img" aria-label="Photo of stacked shipping containers, trucks and a plane"></div>
<svg class="abs" style="left:801px;top:699px" width="276" height="454"><polyline points="0,1 275,1 275,453 0,453" fill="none" stroke="#aaa" stroke-width="1.5"/></svg>
<svg class="abs" style="left:1150px;top:693px" width="50" height="415"><polygon points="50,0 50,415 38,415 0,300 28,215 0,110" fill="var(--salmon)"/></svg>
<h2 class="abs hl about-title">Keeping Your<br><em>Supply Chain</em><br>Moving</h2>
<p class="abs about-text">We deliver a comprehensive range of open-deck and specialized transportation services—including flatbed, step deck, heavy haul, and over-dimensional freight solutions. Backed by years of experience, a trusted nationwide carrier network, and a strong safety-first culture, we provide reliable, adaptable logistics support built around the unique requirements of every load.</p>
<span class="abs btn about-btn">Read More</span>

<!-- services -->
<div class="photo" style="left:0;top:1232px;width:511px;height:668px;background:linear-gradient(160deg,#2f6f82 0%,#5b8f97 40%,#9aa2a3 65%,#3a3e42 100%)" role="img" aria-label="Close-up photo of a silver semi truck front at dusk"></div>
<div class="abs svc-bg"></div>
<h2 class="abs hl svc-title">Our <em>Services</em></h2>
<div class="abs svc-text">
  <p>TQ Freight Global delivers reliable, efficient, and global logistics solutions tailored to your business needs. From freight forwarding to supply chain management, we ensure your cargo moves seamlessly across borders with speed, safety, and precision.</p>
  <p>we connect businesses to the world through smart and dependable logistics services. Our expertise in transportation, warehousing, and global distribution ensures timely deliveries and smooth operations, helping you grow without limits.</p>
</div>
<div class="abs svc-cards">
  <div class="svc-card"><div class="svc-ico"><svg width="34" height="22"><rect x="1" y="11" width="26" height="4" fill="none" stroke="#fff" stroke-width="1.5"/><rect x="22" y="4" width="10" height="11" fill="none" stroke="#fff" stroke-width="1.5"/><circle cx="7" cy="18" r="3" fill="none" stroke="#fff"/><circle cx="27" cy="18" r="3" fill="none" stroke="#fff"/></svg></div><h3>FLATBED TRANSPORTATION</h3><p>From routine shipments to oversized and heavy-haul loads, we handle freight requiring proper securement, regulatory knowledge, and consistent on-time execution.</p></div>
  <div class="svc-card"><div class="svc-ico"><svg width="36" height="22"><rect x="1" y="3" width="24" height="12" fill="none" stroke="#fff" stroke-width="1.5"/><rect x="25" y="7" width="9" height="8" fill="none" stroke="#fff" stroke-width="1.5"/><circle cx="8" cy="18" r="3" fill="none" stroke="#fff"/><circle cx="29" cy="18" r="3" fill="none" stroke="#fff"/></svg></div><h3>STEP DECK TRANSPORTATION</h3><p>Our step deck trucking services support tall, heavy, and specialized freight that requires additional height clearance and flexible loading options.</p></div>
  <div class="svc-card"><div class="svc-ico"><svg width="30" height="30"><line x1="15" y1="2" x2="15" y2="10" stroke="#fff" stroke-width="1.5"/><rect x="5" y="10" width="20" height="12" fill="none" stroke="#fff" stroke-width="1.5"/><circle cx="9" cy="26" r="3" fill="none" stroke="#fff"/><circle cx="21" cy="26" r="3" fill="none" stroke="#fff"/></svg></div><h3>DRY VAN TRANSPORTATION</h3><p>From consumer goods to industrial materials, our dry van services provide the space, security, and consistency you need coast to coast.</p></div>
  <div class="svc-card"><div class="svc-ico"><svg width="34" height="24"><path d="M3 16 L8 6 L26 6 L31 16 Z" fill="none" stroke="#fff" stroke-width="1.5"/><circle cx="10" cy="19" r="3" fill="none" stroke="#fff"/><circle cx="24" cy="19" r="3" fill="none" stroke="#fff"/></svg></div><h3>HEAVY HAUL TRANSPORTATION</h3><p>We provide heavy haul trucking solutions for oversized, overweight, and over-dimensional freight.</p></div>
</div>

<!-- industries -->
<svg class="abs" style="left:0;top:1900px" width="280" height="500"><polygon points="0,0 275,0 110,250 0,150" fill="#e6e6e6"/><polygon points="0,150 110,250 0,480" fill="#fbe4dc"/></svg>
<h2 class="abs hl ind-title">Transportation <em>Industries</em></h2>
<p class="abs ind-text">The transportation industry plays a vital role in connecting economies and enabling global trade. From road and rail to air and sea, it ensures the smooth movement of goods and people across regions. With advanced logistics systems and modern infrastructure, the industry continues to drive efficiency, speed, and reliability in every delivery.</p>
<div class="abs ind-card" style="left:76px"><div class="ph" style="background:linear-gradient(180deg,#b9c3cc,#4d5763)" role="img" aria-label="Photo of a tanker truck"></div><div class="lab o">FOOD &amp; BEVERAGE</div></div>
<div class="abs ind-card" style="left:293px"><div class="ph" style="background:linear-gradient(160deg,#6c7580,#2a2a2c 45%,#b98a5a)" role="img" aria-label="Photo of boxes in a delivery van"></div><div class="lab b">E-COMMERCE &amp; RETAIL</div></div>
<div class="abs ind-card" style="left:505px"><div class="ph" style="background:linear-gradient(180deg,#dfe3e7,#8d949b 60%,#5a5f66)" role="img" aria-label="Photo of a car carrier truck"></div><div class="lab o">MANUFACTURING</div></div>
<div class="abs ind-card" style="left:719px"><div class="ph" style="background:linear-gradient(160deg,#d9dde1,#a9937a 50%,#3a3a3c)" role="img" aria-label="Photo of pallets loaded in a trailer"></div><div class="lab b">PHARMA &amp; HEALTHCARE</div></div>
<div class="abs ind-card" style="left:935px"><div class="ph" style="background:linear-gradient(180deg,#b8c9d8,#d8d8d6 55%,#6a6a6a)" role="img" aria-label="Photo of a white heavy truck at an intersection"></div><div class="lab o">GOVERNMENT SECURED FREIGHT</div></div>

<!-- contact -->
<div class="abs cta-bg"></div>
<h2 class="abs hl cta-title">Let’s Move Your <em>Business Forward</em></h2>
<p class="abs cta-sub">Let's discuss your logistics needs and how we can help your business thrive</p>
<div class="abs form-card"><div style="width:466px;height:100%;background:linear-gradient(180deg,#5f6f86 0%,#e9b35a 45%,#8a7760 70%,#3a3834 100%)" role="img" aria-label="Photo of two white semi trucks parked at sunset"></div></div>
<h2 class="abs hl form-title">Contact Us</h2>
<div class="field" style="left:621px;top:2886px;width:207px;height:48px">First Name</div>
<div class="field" style="left:844px;top:2886px;width:207px;height:48px">Last Name</div>
<div class="field" style="left:621px;top:2952px;width:207px;height:48px">Email</div>
<div class="field" style="left:844px;top:2952px;width:207px;height:48px">Mobile Number</div>
<div class="field" style="left:621px;top:3019px;width:430px;height:99px">Message</div>
<div class="abs submit">SUBMIT</div>

<!-- footer -->
<footer class="abs foot"></footer>
<div class="abs foot-brand"><i></i>TQ Freight Global</div>
<p class="abs foot-about">TQ Freight Global into a dynamic organization focused on solving real logistics challenges, delivering exceptional service, and continuously expanding its capabilities to support businesses across the country.</p>
<div class="abs col" style="left:450px"><h4>Quick Link</h4><ul><li>Home</li><li>Services</li><li>About Us</li><li>Contact Us</li></ul></div>
<div class="abs col" style="left:617px"><h4>Industries</h4><ul><li>Food &amp; Beverage</li><li>E-commerce and Retails</li><li>Manufacturing</li><li>Pharama and Healthcare</li><li>Government Secured Fregiht</li></ul></div>
<div class="abs col enq" style="left:861px"><h4>Enquire Us</h4><ul>
  <li><svg width="16" height="12"><rect x="1" y="1" width="14" height="10" fill="#fff"/><path d="M1 1 L8 7 L15 1" fill="none" stroke="#2b2624" stroke-width="1.3"/></svg>sales@tqfreightglobal.com</li>
  <li><svg width="16" height="16"><rect x="4" y="1" width="9" height="14" rx="2" fill="none" stroke="#fff" stroke-width="1.5"/></svg>(415)-555-0142</li>
  <li><svg width="16" height="16"><circle cx="8" cy="8" r="7" fill="none" stroke="#fff" stroke-width="1.5"/><ellipse cx="8" cy="8" rx="3" ry="7" fill="none" stroke="#fff"/><line x1="1" y1="8" x2="15" y2="8" stroke="#fff"/></svg>www.tqfreightglobal.com</li>
</ul><div class="socials"><span></span><span></span><span></span><span></span></div></div>
<div class="abs bar"><span class="l">© 2026. TQ FREIGHT GLOBAL.All Copyrights.</span><span class="r">Terms and Services &nbsp; Privacy Policy</span></div>

</body>
</html>
```